Im open to ideas.. I was thinking on my business cards aswell as my logo. a place for my name. email. phone number and abn..

ive attched a file with my business logo. which i dont love the colours.. i was think a dark background with charcoal letters so something along those colour schumes but im open to ideas..

BRM Constructions

```html
<!DOCTYPE html>
<html lang="en">
<head>
<meta charset="utf-8">
<title>BRM Constructions — Business Card</title>
<link href="https://fonts.googleapis.com/css2?family=Lato:wght@400;700;900&display=swap" rel="stylesheet">
<style>
  :root {
    --backdrop: #1c1c1c;
    --card: #f4f4f4;
    --ink: #2a2a2a;
    --ink-soft: #3a3a3a;
    --brand-red: #c8101c;
  }
  * { margin: 0; padding: 0; box-sizing: border-box; }
  html, body {
    width: 1200px;
    height: 873px;
    overflow: hidden;
    background: var(--backdrop);
    font-family: "Lato", sans-serif;
  }
  .canvas {
    position: relative;
    width: 1200px;
    height: 873px;
  }
  .business-card {
    position: absolute;
    left: 220px;
    top: 216px;
    width: 760px;
    height: 440px;
    border-radius: 22px;
    background: linear-gradient(135deg, #ffffff 0%, var(--card) 60%, #e9e9e9 100%);
    box-shadow: 0 18px 40px rgba(0, 0, 0, 0.55);
  }
  .brand {
    position: absolute;
    left: 56px;
    top: 62px;
    display: flex;
    align-items: center;
    gap: 14px;
  }
  .brand-mark {
    width: 22px;
    height: 22px;
    background: var(--brand-red);
  }
  .brand-name {
    font-weight: 900;
    font-size: 40px;
    letter-spacing: 1px;
    color: var(--ink);
    text-transform: uppercase;
  }
  .holder {
    position: absolute;
    right: 56px;
    top: 196px;
    text-align: right;
  }
  .holder-name {
    font-weight: 700;
    font-size: 22px;
    color: var(--brand-red);
  }
  .holder-role {
    font-size: 14px;
    color: var(--ink-soft);
    margin-top: 2px;
  }
  .contacts {
    position: absolute;
    left: 56px;
    bottom: 46px;
    list-style: none;
  }
  .contact-item {
    display: flex;
    align-items: center;
    gap: 10px;
    font-size: 18px;
    color: var(--ink-soft);
    margin-bottom: 12px;
  }
  .contact-icon {
    width: 20px;
    height: 20px;
    flex: none;
  }
  .contact-web {
    font-weight: 900;
    font-size: 21px;
    color: var(--brand-red);
    margin-top: 6px;
  }
</style>
</head>
<body>
<main class="canvas">
  <section class="business-card" aria-label="BRM Constructions business card">
    <div class="brand">
      <span class="brand-mark"></span>
      <span class="brand-name">BRM Constructions</span>
    </div>

    <div class="holder">
      <p class="holder-name">Daniel Hartley</p>
      <p class="holder-role">Owner / Founder</p>
    </div>

    <ul class="contacts">
      <li class="contact-item">
        <svg class="contact-icon" viewBox="0 0 24 24" aria-hidden="true">
          <path fill="#c8101c" d="M3 9c0-3 4-5 9-5s9 2 9 5v2h-5V9c-1-.8-2.5-1.2-4-1.2S9 8.2 8 9v2H3z"/>
          <path fill="#c8101c" d="M6 13h12l2 7H4z"/>
          <circle cx="12" cy="16.5" r="2" fill="#f4f4f4"/>
        </svg>
        <span>0412555019</span>
      </li>
      <li class="contact-item">
        <svg class="contact-icon" viewBox="0 0 24 24" aria-hidden="true">
          <rect x="2" y="5" width="20" height="14" rx="1.5" fill="#c8101c"/>
          <path d="M3 6l9 7 9-7" fill="none" stroke="#f4f4f4" stroke-width="1.6"/>
        </svg>
        <span>info@brmconstructions.com</span>
      </li>
      <li class="contact-web">www.brmconstructions.com</li>
    </ul>
  </section>
</main>
</body>
</html>
```